Wandering Rooms Stationary Set

Wandering Rooms is a bespoke interior design firm set to provide services to VIP clients with elegance and minimalism is the main theme for our stationary set. We require a full stationary set covering A4 letterhead, A4 & A3 envelopes, business cards, USB's, CDs, email signature and any other item the designer sees fit. logo is already designed and finalized, and we require the designer to use it as is without modifying the logo.

Address to be used on letterhead / business cards ...etc shall be as follows:

Phone : +971 2 518 2047
P.O. Box : 309186
Address: Block C&D, Bldg. 47, Court 12, Abu Dhabi, United Arab Emirates
Website: www.wanderingrooms-example.com

Target Market(s)

VIP Clients

Industry/Entity Type

Interior Design

Font styles to use
Other font styles liked:
• something to be unique

Colors

Designer to choose colors to be used in the design.

Requirements
Must have
• Elegant, minimalistic
Nice to have
• Simple yet elegant design having a sharp yet clean cut format
Should not have
• No additional colours, just colours that are used in the logo (silver, black or gold)

```html
<!DOCTYPE html>
<html lang="en">
<head>
<meta charset="utf-8">
<title>Wandering Rooms Stationery Set</title>
<link rel="stylesheet" href="https://fonts.googleapis.com/css2?family=Lato:wght@300;400;700&family=Roboto:wght@400;500&family=Pinyon+Script&display=swap">
<style>
  :root {
    --gold: #b0945a;
    --gold-light: #bd9f63;
    --charcoal: #4b4b4b;
    --ink: #3a3a3a;
    --paper: #ffffff;
    --paper-shade: #f3f3f3;
    --backdrop: #e9e7e3;
  }
  * { box-sizing: border-box; margin: 0; padding: 0; }
  html, body { width: 1200px; height: 945px; overflow: hidden; }
  body { background: var(--backdrop); font-family: "Lato", sans-serif; color: var(--ink); position: relative; }
  .icons { position: absolute; width: 0; height: 0; }

  .sheet { position: absolute; background: linear-gradient(135deg, var(--paper), var(--paper-shade)); box-shadow: 0 2px 8px rgba(0,0,0,.12); overflow: hidden; }

  .wordmark { font-family: "Lato", sans-serif; font-weight: 400; text-transform: uppercase; letter-spacing: .22em; color: var(--gold); white-space: nowrap; }
  .wordmark--light { color: var(--paper); }

  .contact-list { list-style: none; font-family: "Roboto", sans-serif; }
  .contact-list li { display: flex; align-items: center; gap: 4px; line-height: 1.3; }
  .contact-list svg { flex: none; fill: var(--gold); }
  .contact-list--light svg { fill: var(--paper); }

  /* Letterhead */
  .letterhead { left: 40px; top: 55px; width: 560px; height: 792px; }
  .letterhead .wordmark { position: absolute; left: 45px; top: 70px; font-size: 15px; }
  .letterhead .contact-list { position: absolute; right: 48px; top: 48px; font-size: 9px; color: var(--ink); }
  .letterhead .contact-list svg { width: 7px; height: 7px; }
  .letterhead .edge-tab { position: absolute; right: 0; top: 42px; width: 6px; height: 40px; background: var(--charcoal); }
  .letter-body { position: absolute; left: 60px; top: 165px; width: 440px; font-size: 8.6px; line-height: 1.42; color: #555; }
  .letter-body .date { margin-bottom: 16px; }
  .letter-body .recipient { margin-bottom: 24px; }
  .letter-body .recipient strong { color: var(--ink); font-weight: 700; }
  .letter-body .greeting { margin-bottom: 14px; }
  .letter-body p.copy { text-align: justify; margin-bottom: 14px; }
  .letter-body .closing { margin-top: 30px; }
  .signature { font-family: "Pinyon Script", cursive; font-size: 19px; color: #222; margin-top: 4px; }
  .letterhead .footer-band { position: absolute; left: 0; bottom: 0; width: 560px; height: 150px; }
  .letterhead .footer-address { position: absolute; left: 0; right: 0; bottom: 16px; text-align: center; font-family: "Roboto", sans-serif; font-size: 9px; color: var(--paper); }

  /* DL envelope front */
  .envelope-front { left: 630px; top: 40px; width: 530px; height: 230px; }
  .envelope-front .wordmark { position: absolute; left: 30px; top: 55px; font-size: 12px; }
  .envelope-front .contact-list { position: absolute; left: 30px; top: 140px; font-size: 7.5px; color: var(--ink); }
  .envelope-front .contact-list svg { width: 6px; height: 6px; }
  .envelope-front .address { position: absolute; left: 30px; top: 185px; font-family: "Roboto", sans-serif; font-size: 7.5px; line-height: 1.35; color: var(--ink); }
  .envelope-front .edge-tab { position: absolute; left: 0; top: 140px; width: 5px; height: 60px; background: var(--charcoal); }
  .curve-art { position: absolute; top: 0; left: 0; }

  /* Business cards */
  .card { width: 255px; height: 146px; top: 295px; }
  .card-front { left: 630px; }
  .card-front .wordmark { position: absolute; left: 14px; top: 66px; font-size: 8.5px; letter-spacing: .16em; }
  .card-front .details { position: absolute; left: 150px; top: 34px; color: var(--paper); font-family: "Roboto", sans-serif; }
  .card-front .name { font-size: 8px; font-weight: 500; }
  .card-front .role { font-size: 5.5px; margin-bottom: 10px; }
  .card-front .addr { font-size: 5.5px; line-height: 1.3; margin-bottom: 9px; }
  .card-front .contact-list { font-size: 5.5px; }
  .card-front .contact-list svg { width: 5px; height: 5px; }
  .card-back { left: 905px; background: linear-gradient(135deg, var(--gold-light), var(--gold)); }
  .card-back .wordmark { position: absolute; left: 0; right: 0; top: 58px; text-align: center; font-size: 13px; }
  .card-back .site-rule { position: absolute; left: 18px; right: 18px; bottom: 18px; display: flex; align-items: center; gap: 8px; font-family: "Roboto", sans-serif; font-size: 5px; color: var(--paper); }
  .card-back .site-rule::before, .card-back .site-rule::after { content: ""; flex: 1; height: 1px; background: var(--paper); }

  /* DL envelope back */
  .envelope-back { left: 630px; top: 470px; width: 530px; height: 230px; }
  .envelope-back .flap { position: absolute; top: 0; left: 0; }
  .envelope-back .wordmark { position: absolute; left: 0; right: 0; top: 30px; text-align: center; font-size: 11px; }
</style>
</head>
<body>

<svg class="icons" aria-hidden="true">
  <symbol id="icon-phone" viewBox="0 0 10 10"><path d="M2 .5 3.6 2.6 2.7 3.6c.6 1.5 2 2.9 3.7 3.7l1-.9L9.5 8l-1 1.5C4.5 9.5.5 5.5.5 1.5Z"/></symbol>
  <symbol id="icon-mail" viewBox="0 0 10 10"><path d="M.5 2h9v6h-9Zm1 1v.3L5 5.6l3.5-2.3V3Zm0 1.5V7h7V4.5L5 6.8Z"/></symbol>
  <symbol id="icon-globe" viewBox="0 0 10 10"><circle cx="5" cy="5" r="4.5"/></symbol>
</svg>

<!-- A4 letterhead -->
<section class="sheet letterhead">
  <div class="wordmark">Wandering Rooms</div>
  <ul class="contact-list">
    <li><svg><use href="#icon-phone"/></svg>+971 2 518 2047</li>
    <li><svg><use href="#icon-mail"/></svg>info@wanderingrooms-example.com</li>
    <li><svg><use href="#icon-globe"/></svg>www.wanderingrooms-example.com</li>
  </ul>
  <div class="edge-tab"></div>

  <div class="letter-body">
    <p class="date">01 January 2050</p>
    <p class="recipient"><strong>Company (Pvt) Ltd.</strong><br>PO Box 3355 Mainville St<br>Sample City Country 3355</p>
    <p class="greeting">Dear Daniel Mercer,</p>
    <p class="copy">Lorem ipsum dolor sit amet, consectetuer adipiscing elit, sed diam nonummy nibh euismod tincidunt ut laoreet dolore magna aliquam erat volutpat. Ut wisi enim ad minim veniam, quis nostrud exerci tation ullamcorper suscipit lobortis nisl ut aliquip ex ea commodo consequat. Duis dolore te feugait nulla facilisi. Nam liber tempor cum soluta nobis eleifend option congue nihil imperdiet doming id quod mazim placerat facer possim assum. Lorem ipsum dolor sit amet, consectetuer adipiscing elit, sed diam nonummy nibh euismod tincidunt ut laoreet dolore magna aliquam erat volutpat. Ut wisi enim ad minim veniam, quis nostrud exerci tation ullamcorper suscipit lobortis nisl ut aliquip ex ea commodo consequat.</p>
    <p class="copy">Consectetuer adipiscing elit, sed diam nonummy nibh euismod tincidunt ut laoreet dolore magna aliquam erat volutpat. Ut wisi enim ad minim veniam, quis nostrud exerci tation ullamcorper suscipit lobortis nisl ut aliquip ex ea commodo consequat. Consectetuer adipiscing elit, sed diam nonummy nibh euismod tincidunt ut laoreet dolore magna aliquam erat volutpat. Ut wisi enim ad minim veniam, quis nostrud exerci tation ullamcorper suscipit lobortis nisl ut aliquip ex ea commodo consequat.</p>
    <p class="copy">Consectetuer adipiscing elit, sed diam nonummy nibh euismod tincidunt ut laoreet dolore magna aliquam erat volutpat. Ut wisi enim ad minim veniam, quis nostrud exerci tation ullamcorper suscipit lobortis nisl ut aliquip ex ea commodo consequat. Consectetuer adipiscing elit, sed diam nonummy nibh euismod tincidunt ut laoreet dolore magna aliquam erat volutpat. Ut wisi enim ad minim veniam, quis nostrud exerci tation ullamcorper suscipit lobortis nisl ut aliquip ex ea commodo consequat.</p>
    <p class="closing">Sincerely Yours</p>
    <p class="signature">Thomas Edward Larkin</p>
  </div>

  <svg class="footer-band" viewBox="0 0 560 150" aria-hidden="true">
    <path d="M18 66 Q260 134 560 26 L560 36 Q260 144 18 66 Z" fill="var(--charcoal)"/>
    <path d="M0 70 Q260 150 560 44 L560 150 L0 150 Z" fill="var(--gold)"/>
  </svg>
  <p class="footer-address">P.O. Box : 309186, Block C&amp;D, Bldg. 47, Court 12, Abu Dhabi, UAE</p>
</section>

<!-- DL envelope, front -->
<section class="sheet envelope-front">
  <svg class="curve-art" width="530" height="230" viewBox="0 0 530 230" aria-hidden="true">
    <path d="M443 0 Q520 110 402 230 L420 230 Q508 120 452 0 Z" fill="var(--charcoal)"/>
    <path d="M458 0 Q534 112 428 230 L530 230 L530 0 Z" fill="var(--gold)"/>
  </svg>
  <div class="wordmark">Wandering Rooms</div>
  <div class="edge-tab"></div>
  <ul class="contact-list">
    <li><svg><use href="#icon-phone"/></svg>+971 2 518 2047</li>
    <li><svg><use href="#icon-mail"/></svg>info@wanderingrooms-example.com</li>
    <li><svg><use href="#icon-globe"/></svg>www.wanderingrooms-example.com</li>
  </ul>
  <p class="address">P.O. Box : 309186, Block C&amp;D, Bldg. 47,<br>Court 12, Abu Dhabi, UAE</p>
</section>

<!-- Business card, front -->
<section class="sheet card card-front">
  <svg class="curve-art" width="255" height="146" viewBox="0 0 255 146" aria-hidden="true">
    <path d="M120 0 Q165 70 98 146 L108 146 Q160 75 127 0 Z" fill="var(--charcoal)"/>
    <path d="M132 0 Q170 75 114 146 L255 146 L255 0 Z" fill="var(--gold)"/>
  </svg>
  <div class="wordmark">Wandering Rooms</div>
  <div class="details">
    <p class="name">Adam Corwell</p>
    <p class="role">Managing Director</p>
    <p class="addr">P.O. Box : 309186<br>Block C&amp;D, Bldg. 47, Court 12<br>Abu Dhabi, United Arab Emirates</p>
    <ul class="contact-list contact-list--light">
      <li><svg><use href="#icon-phone"/></svg>+971 2 518 2047</li>
      <li><svg><use href="#icon-mail"/></svg>info@wanderingrooms-example.com</li>
      <li><svg><use href="#icon-globe"/></svg>www.wanderingrooms-example.com</li>
    </ul>
  </div>
</section>

<!-- Business card, back -->
<section class="sheet card card-back">
  <div class="wordmark wordmark--light">Wandering Rooms</div>
  <p class="site-rule">www.wanderingrooms-example.com</p>
</section>

<!-- DL envelope, back -->
<section class="sheet envelope-back">
  <svg class="flap" width="530" height="230" viewBox="0 0 530 230" aria-hidden="true">
    <path d="M0 0 H530 V60 Q530 80 505 86 L265 92 L25 86 Q0 80 0 60 Z" fill="var(--gold)"/>
    <path d="M25 86 L265 92 L505 86" fill="none" stroke="#e2e2e2" stroke-width="1"/>
  </svg>
  <div class="wordmark wordmark--light">Wandering Rooms</div>
</section>

</body>
</html>
```